Business Card Design Project

This is the first time we use our new logo. We need a business card that we can use both on our institutional corporate relationships and also that works for our staff that deals with consumers directly.

VELUNDA is a new company dedicated to empower consumers and to provide them with the best choices for specialized health care using the latest telemedicine technology (medicine at a distance via videoconference).

We want to print this cards in high quality materials and process. We will like designs that allow us to use UV spot varnish and other techniques that will differentiate us.

We are including Two different versions of Color logos. In addition we are including white over black background logos. Those can be used replacing the black for a color.

Please note this is the first time we will be creating any corporate materials with our new logo and colors.

Target Market(s)

34+ consumers of medium high and high socioeconomic levels.

Industry/Entity Type

Health

Requirements
Must have
• Our logo on its original colors
Should not have
• Any other graphical element or design that is not our logo

```html
<!DOCTYPE html>
<html lang="en">
<head>
<meta charset="utf-8">
<title>VELUNDA — Business Card</title>
<link rel="stylesheet" href="https://fonts.googleapis.com/css2?family=Josefin+Sans:wght@400;600;700&family=Cinzel:wght@600;700&display=swap">
<style>
  :root {
    --backdrop: #5e3a22;
    --silver-light: #e9e9ea;
    --silver-mid: #bfc0c2;
    --silver-dark: #8e8f92;
    --ink-black: #070708;
    --navy: #15233a;
    --accent-blue: #6fa8d8;
    --soft-blue: #a9cdee;
    --mauve: #b9aab4;
    --white: #ffffff;
  }
  * { margin: 0; padding: 0; box-sizing: border-box; }
  html, body {
    width: 1200px; height: 750px; overflow: hidden;
    background: var(--backdrop);
  }
  .canvas { position: relative; width: 1200px; height: 750px; }
  .card {
    position: absolute; left: 289px; width: 622px; height: 330px;
    border-radius: 22px; overflow: hidden;
    background: linear-gradient(120deg, var(--silver-dark) 0%, var(--silver-light) 45%, var(--silver-mid) 100%);
  }
  .card--front { top: 36px; }
  .card--back { top: 388px; }
  .card__shape { position: absolute; inset: 0; }

  .brand-name {
    position: absolute;
    font-family: "Josefin Sans", sans-serif; font-weight: 700;
    color: var(--white); letter-spacing: 2px; line-height: 1;
  }
  .brand-dot { position: absolute; border-radius: 50%; background: var(--white); }

  .card--front .brand-dot { left: 70px; top: 34px; width: 92px; height: 92px; }
  .card--front .brand-name { left: 206px; top: 92px; font-size: 54px; }

  .holder { position: absolute; left: 0; right: 0; top: 176px; text-align: center; }
  .holder__name {
    font-family: "Cinzel", serif; font-weight: 700; font-size: 26px;
    color: var(--accent-blue); letter-spacing: 1px;
  }
  .holder__role {
    font-family: "Cinzel", serif; font-weight: 600; font-size: 12px;
    color: var(--accent-blue); letter-spacing: 1px; margin-top: -2px;
  }
  .contact {
    position: absolute; font-family: "Josefin Sans", sans-serif;
    font-size: 18px; font-variant: small-caps; white-space: nowrap; line-height: 1;
  }
  .contact__label { color: var(--accent-blue); }
  .contact__value { color: var(--white); }
  .contact--address { left: 73px; top: 240px; }
  .contact--mobile { left: 310px; top: 240px; }
  .contact--email { left: 73px; top: 263px; }
  .contact--fax { left: 320px; top: 263px; }
  .contact--web { left: 190px; top: 289px; }

  .card--back .brand-dot { left: 126px; top: 76px; width: 84px; height: 84px; }
  .card--back .brand-name { left: 30px; width: 250px; text-align: center; top: 193px; font-size: 48px; }
  .note-lines { position: absolute; left: 381px; top: 88px; }
  .note-lines span {
    display: block; width: 6px; height: 2px; background: var(--accent-blue);
    margin-bottom: 26px;
  }
</style>
</head>
<body>
<main class="canvas">
  <section class="card card--front" aria-label="Card front">
    <svg class="card__shape" width="622" height="330" viewBox="0 0 622 330" aria-hidden="true">
      <path d="M0,198 Q311,118 622,192 V330 H0 Z" fill="var(--mauve)"/>
      <path d="M0,207 Q311,128 622,201 V330 H0 Z" fill="var(--ink-black)"/>
    </svg>
    <span class="brand-dot" aria-hidden="true"></span>
    <span class="brand-name">VELUNDA</span>
    <div class="holder">
      <p class="holder__name">Daren Molek</p>
      <p class="holder__role">President</p>
    </div>
    <p class="contact contact--address"><span class="contact__label">Adress:</span> <span class="contact__value">Tarvin Oslak</span></p>
    <p class="contact contact--mobile"><span class="contact__label">Mobile:</span> <span class="contact__value">38970 518 642</span></p>
    <p class="contact contact--email"><span class="contact__label">E-mail:</span> <span class="contact__value">dmolek@mail.com</span></p>
    <p class="contact contact--fax"><span class="contact__label">Fax:</span> <span class="contact__value">38971 204 956</span></p>
    <p class="contact contact--web"><span class="contact__label">Website:</span> <span class="contact__value">www.velunda.com</span></p>
  </section>

  <section class="card card--back" aria-label="Card back">
    <svg class="card__shape" width="622" height="330" viewBox="0 0 622 330" aria-hidden="true">
      <path d="M0,0 H268 Q462,165 274,330 H0 Z" fill="var(--soft-blue)"/>
      <path d="M0,0 H257 Q452,165 263,330 H0 Z" fill="var(--navy)"/>
    </svg>
    <span class="brand-dot" aria-hidden="true"></span>
    <span class="brand-name">VELUNDA</span>
    <div class="note-lines" aria-hidden="true">
      <span></span><span></span><span></span><span></span><span></span><span></span>
    </div>
  </section>
</main>
</body>
</html>
```